Business Card for Field Lotus-Eco Friendly Organic Clothing Brand

We are looking for an amazing business card for our eco friendly, organic clothing brand. We are thinking maybe a business card with a peel off sticker on the back, since our hanging clothing tag is a peel off sticker on the back. I will attach our hang tag so we can make sure we stay in line with our design. I've also attached a bag we are doing because I do like the scattered emblem look as well.

```html
<!DOCTYPE html>
<html lang="en">
<head>
<meta charset="utf-8">
<title>Field Lotus Business Card</title>
<link href="https://fonts.googleapis.com/css2?family=Open+Sans:wght@400;600&display=swap" rel="stylesheet">
<style>
  :root {
    --backdrop: #161616;
    --card: #ffffff;
    --gold: #cf9a2a;
    --ink: #3a3a3a;
    --muted: #555555;
  }
  * { margin: 0; padding: 0; box-sizing: border-box; }
  html, body { width: 1200px; height: 900px; overflow: hidden; }
  body {
    background: var(--backdrop);
    font-family: "Open Sans", Arial, sans-serif;
    position: relative;
  }
  .card {
    position: absolute;
    background: var(--card);
    border-radius: 10px;
  }
  .card--front { left: 149px; top: 306px; width: 439px; height: 270px; }
  .card--back  { left: 608px; top: 306px; width: 441px; height: 272px; }

  .brand {
    position: absolute;
    display: flex;
    align-items: center;
    gap: 10px;
    color: var(--gold);
    font-weight: 600;
    white-space: nowrap;
  }
  .brand__mark {
    width: 16px; height: 16px;
    background: var(--gold);
  }
  .card--front .brand { left: 40px; top: 117px; font-size: 26px; }
  .card--back .brand { left: 0; right: 0; top: 114px; justify-content: center; font-size: 30px; }
  .card--back .brand__mark { width: 18px; height: 18px; }

  .brand-url {
    position: absolute;
    color: var(--gold);
    font-size: 8px;
  }
  .card--front .brand-url { left: 98px; top: 156px; }
  .card--back .brand-url { left: 0; right: 0; top: 158px; text-align: center; }

  .contact { position: absolute; left: 255px; top: 68px; color: var(--ink); }
  .contact__name { color: var(--gold); font-size: 14.5px; font-weight: 600; line-height: 19px; }
  .contact__title { font-size: 12px; line-height: 16px; }
  .contact__address { margin-top: 10px; font-size: 12px; line-height: 16px; }
  .contact__list { margin-top: 12px; list-style: none; font-size: 12px; line-height: 16px; }
  .contact__list li { display: flex; align-items: center; gap: 8px; }
  .contact__list svg { width: 8px; height: 8px; fill: var(--gold); flex: none; }
</style>
</head>
<body>
  <section class="card card--front">
    <div class="brand"><span class="brand__mark"></span>Field Lotus</div>
    <div class="brand-url">www.fieldlotus.com</div>

    <div class="contact">
      <p class="contact__name">Daniel Reed</p>
      <p class="contact__title">Managing Director</p>
      <p class="contact__address">12345, Address Goes Here<br>Country Name, 123456.</p>
      <ul class="contact__list">
        <li><svg viewBox="0 0 10 10"><path d="M2 0.5l2 2-1 1.2c.6 1.3 1.6 2.3 2.9 2.9L7 5.5l2 2-1.3 1.8C4 9 1 6 .7 2.2z"/></svg>044-123 456 789</li>
        <li><svg viewBox="0 0 10 10"><path d="M0 2h10v6H0z M0 2l5 3.5L10 2" /></svg>info@webname.com</li>
        <li><svg viewBox="0 0 10 10"><circle cx="5" cy="5" r="5"/></svg>www.websitename.com</li>
      </ul>
    </div>
  </section>

  <section class="card card--back">
    <div class="brand"><span class="brand__mark"></span>Field Lotus</div>
    <div class="brand-url">www.fieldlotus.com</div>
  </section>
</body>
</html>
```